Business Card Design

We like to use greens as you will see in our logo (but not TOO much green). We are a Dental Clinic in a somewhat eccentric community. We do not like the dated sharp designs which we see many dentists use. We're looking for something bright and fresh while still maintaining the integrity of the profession. Elegance is not necessarily what we are going for... we need for the design to be "mature" but also up-lifting.

See our logo.
Updates

Project Deadline Extended
Reason: We have 5 designs which we like. But we'd like to see a few more before committing to a design.

Project Deadline Extended
Reason: We are awaiting revisions to this project. We are still welcoming designs while we wait to see if designers are able to provide to us the revisions we require in order to proceed with a selection.

Target Market(s)

Younger families - ages late 20's to early 40's

Industry/Entity Type

Business

Contact Information for Business Card

Corwel T. Banfry DDS 2730 W. Halvert Rd. Ste. 7 Fernhollow, WA 98391 (360)555-0174 FX (360)555-0189 info@BrightwellDentalCareWa.com BrigthwellDentalCareWa.com on the back of the card we need an appointment reminder (For____ Date___ Time____) with "If you are unable to keep your appointment, kindly give 48 hours notice" at the bottom. No use of teeth in the design. DOUBLE SIDED DESIGN

Requirements
Should not have
• The use of pictures of teeth

```html
<!DOCTYPE html>
<html lang="en">
<head>
<meta charset="utf-8">
<title>Brightwell Dental Care – Business Card</title>
<link rel="stylesheet" href="https://fonts.googleapis.com/css2?family=Open+Sans:wght@400;600;700&family=Tinos:ital,wght@0,400;0,700;1,400&display=swap">
<style>
  :root {
    --stage: #ecebe6;
    --paper: #ffffff;
    --forest: #2f7a12;
    --lime: #9ed92b;
    --lime-soft: #c8ec7a;
    --ink: #555555;
    --rule: #8a8a8a;
  }
  * { margin: 0; padding: 0; box-sizing: border-box; }
  html, body { width: 1200px; height: 492px; overflow: hidden; }
  body {
    background: var(--stage);
    position: relative;
    font-family: "Open Sans", Arial, sans-serif;
  }
  .card {
    position: absolute;
    top: 86px;
    width: 540px;
    height: 320px;
    background: var(--paper);
    box-shadow: 0 4px 14px rgba(0,0,0,0.18);
    overflow: hidden;
  }
  .card--front { left: 40px; }
  .card--back { left: 620px; }

  .front-panel { position: absolute; inset: 0; }
  .brand-name {
    position: absolute;
    color: var(--forest);
    font-family: "Open Sans", Arial, sans-serif;
    font-weight: 600;
    line-height: 1.05;
  }
  .card--front .brand-name { left: 38px; top: 120px; font-size: 34px; }
  .brand-name .brand-mark {
    display: inline-block;
    width: 16px; height: 16px;
    border-radius: 50%;
    background: var(--forest);
    margin-right: 10px;
    vertical-align: middle;
  }
  .contact {
    position: absolute;
    right: 26px;
    top: 34px;
    width: 230px;
    text-align: right;
    color: #fff;
  }
  .contact__name { font-size: 17px; font-weight: 700; margin-bottom: 22px; }
  .contact__address { font-size: 12px; line-height: 1.5; margin-bottom: 30px; }
  .contact__line {
    font-size: 12px;
    line-height: 1.75;
    display: flex;
    justify-content: flex-end;
    align-items: center;
    gap: 5px;
    white-space: nowrap;
  }
  .contact__line svg { width: 11px; height: 11px; flex: none; }

  .card--back .brand-name { left: 36px; top: 70px; font-size: 26px; }
  .appointment {
    position: absolute;
    left: 36px;
    top: 200px;
    width: 470px;
    font-family: "Tinos", "Times New Roman", serif;
    color: var(--ink);
  }
  .appointment__title {
    color: var(--forest);
    font-weight: 700;
    font-size: 15px;
    letter-spacing: 0.3px;
    display: flex;
    align-items: flex-end;
    gap: 8px;
  }
  .appointment__title::after {
    content: "";
    flex: 1;
    border-bottom: 1px dotted var(--rule);
    margin-bottom: 4px;
    margin-right: 110px;
  }
  .field-row {
    display: flex;
    align-items: flex-end;
    gap: 6px;
    font-family: "Open Sans", Arial, sans-serif;
    font-size: 13px;
    margin-top: 12px;
  }
  .field-line { border-bottom: 1px solid var(--rule); height: 1px; margin-bottom: 4px; }
  .field-line--dotted { border-bottom-style: dotted; }
  .field-line--name { width: 290px; }
  .field-line--date { width: 95px; }
  .field-line--time { width: 85px; }
  .field-label--time { margin-left: 14px; }
  .appointment__note {
    font-style: italic;
    font-size: 15px;
    margin-top: 14px;
    white-space: nowrap;
  }
</style>
</head>
<body>

  <section class="card card--front" aria-label="Card front">
    <svg class="front-panel" viewBox="0 0 540 320" preserveAspectRatio="none" aria-hidden="true">
      <path d="M292 0 C322 60 322 130 300 190 C284 240 292 290 310 320 L540 320 L540 0 Z" fill="var(--forest)"/>
      <path d="M280 0 C312 60 314 130 292 190 C276 240 284 290 302 320" fill="none" stroke="var(--lime)" stroke-width="4"/>
      <path d="M288 0 C318 60 320 130 298 190 C282 240 290 290 308 320" fill="none" stroke="var(--lime-soft)" stroke-width="2"/>
    </svg>

    <div class="brand-name"><span class="brand-mark"></span>Brightwell<br>Dental Care</div>

    <div class="contact">
      <p class="contact__name">Corwel T. Banfry, DDS</p>
      <p class="contact__address">2730 W. Halvert Rd. Ste.<br>7 Fernhollow, WA 98391</p>
      <p class="contact__line">
        <svg viewBox="0 0 12 12"><circle cx="6" cy="6" r="5.3" fill="none" stroke="#fff"/><path d="M4 3.2 L5.2 4.6 L4.6 5.4 Q5.5 7 6.8 7.6 L7.6 7 L8.8 8.2 L8 9 Q5 8.5 3.4 4 Z" fill="#fff"/></svg>
        (360) 555-0174
      </p>
      <p class="contact__line">
        <svg viewBox="0 0 12 12"><rect x="1" y="4" width="10" height="6" rx="1" fill="#fff"/><rect x="3" y="1.5" width="6" height="3" fill="none" stroke="#fff"/></svg>
        (360) 555-0189
      </p>
      <p class="contact__line">
        <svg viewBox="0 0 12 12"><rect x="1" y="2.5" width="10" height="7" rx="1" fill="#fff"/><path d="M1.5 3 L6 6.5 L10.5 3" fill="none" stroke="var(--forest)"/></svg>
        info@BrightwellDentalCareWa.com
      </p>
      <p class="contact__line">
        <svg viewBox="0 0 12 12"><circle cx="6" cy="6" r="5" fill="none" stroke="#fff"/><ellipse cx="6" cy="6" rx="2.2" ry="5" fill="none" stroke="#fff"/><path d="M1 6 H11" stroke="#fff"/></svg>
        www.BrigthwellDentalCareWa.com
      </p>
    </div>
  </section>

  <section class="card card--back" aria-label="Card back">
    <div class="brand-name"><span class="brand-mark"></span>Brightwell<br>Dental Care</div>

    <div class="appointment">
      <h2 class="appointment__title">YOUR APPOINTMENT</h2>
      <div class="field-row">
        <span>Name :</span>
        <span class="field-line field-line--dotted field-line--name"></span>
      </div>
      <div class="field-row">
        <span>Date :</span>
        <span class="field-line field-line--date"></span>
        <span class="field-label--time">Time :</span>
        <span class="field-line field-line--time"></span>
        <span>am / pm</span>
      </div>
      <p class="appointment__note">If you are unable to keep your appointment, kindly give 48 hours notice</p>
    </div>
  </section>

</body>
</html>
```